Create a Brochure Design for Brantley Homecare

Brantley Homecare is a subsidiary of the Brantley Care Group. This brochure is specifically for the Brantley Homecare company and brand. Create a 3 panel, A4, front and back, tri-fold brochure. This brochure will be a way to introduce our Homecare services to the community, prospective clients, and various referral partners. The brochure must be eye catching, unique in its deliverables and demonstrate both attention to detail and comfort. Our organization is sophisticated and built around warmth, care and individualized personal attention. The most important aspect of this design is to focus on creating a nurturing, warm, and inviting feel where you would want to have a Nurse or Nurse’s Aide in your own home or a loved one’s home.

I am open to the creativity of the designer to develop something based on the above criteria; however I would like the design to work well with the existing collateral material. What I mean by that is that while I want everything to have its own personality and stand out as its own brand representative, I still need to be able to tell that the overall design concept stays stylistically inside of the same ‘family’ of existing designed material. Because of this, below I would like for the designer to pull inspiration from the link to our website (Located below) as well as from the attachment of our recently refreshed business cards (Attached). This should allow each design to be unique and creative, while still staying inside of a framework and the feel/style that I am looking for.

Finally, I want all the designers to understand that this brochure design is for a private, in home, healthcare company where we are responsible for providing personalized care for a culturally and ethnically diverse make-up clientele of all ages. The photos that are used must represent an image of warmth, care, and a positive interaction between client and caregiver.

Look under the Brantley Homecare tab at www.brantleycaregroup.example

Industry/Entity Type

Healthcare

Requirements
Must have
• • The Brantley Homecare company logo must be included.

```html
<!DOCTYPE html>
<html lang="en">
<head>
<meta charset="utf-8">
<title>Brantley Homecare Tri-fold Brochure</title>
<link rel="stylesheet" href="https://fonts.googleapis.com/css2?family=PT+Sans:ital,wght@0,400;0,700;1,400&display=swap">
<style>
  :root{
    --teal:#4e9393;
    --teal-light:#8fc0bf;
    --teal-dark:#2f7373;
    --salmon:#f5978c;
    --salmon-soft:#f8b3aa;
    --coral:#f0675a;
    --green-dark:#1f5d4f;
    --green-pale:#c9dcb3;
    --ink:#231f20;
    --white:#ffffff;
    --gray-dark:#2c2c2c;
    --gray-mid:#8a8a8a;
    --page:#ffffff;
  }
  *{box-sizing:border-box;margin:0;padding:0}
  html,body{width:1120px;height:1200px;overflow:hidden;background:var(--page)}
  body{position:relative;font-family:"PT Sans",Arial,sans-serif;color:var(--ink)}

  .sheet{position:absolute;left:216px;width:700px;height:482px;display:flex;border:1px solid #d8d8d8;box-shadow:0 2px 6px rgba(0,0,0,.18);overflow:hidden}
  .sheet--outside{top:95px}
  .sheet--inside{top:622px}
  .panel{position:relative;width:233.33px;height:100%;overflow:hidden;font-size:8.4px;line-height:1.3}
  .panel + .panel{border-left:1px solid rgba(0,0,0,.12)}
  .decor{position:absolute;left:0;width:100%;display:block}
  .decor--top{top:0}
  .decor--bottom{bottom:0}
  .url{position:absolute;right:12px;bottom:8px;font-size:5.5px;color:var(--white);letter-spacing:.2px;z-index:3}

  .wordmark{position:absolute;display:flex;align-items:center;gap:3px;font-size:10px;font-weight:700;color:var(--teal-dark);z-index:3}
  .wordmark__dot{width:7px;height:7px;background:var(--salmon)}
  .wordmark--dark{color:var(--ink)}

  .photo{position:absolute}
  .content{position:absolute;left:12px;right:12px;z-index:2}

  /* Outside sheet */
  .panel--services{background:var(--teal)}
  .services-list p{color:var(--white);margin-bottom:6px}
  .services-list .label{color:var(--coral);font-weight:700}
  .photo-strip{position:absolute;left:0;top:171px;width:461px;height:95px;z-index:4}
  .photo-strip .photo{top:0;height:95px}
  .schedule h2{color:var(--coral);font-size:13px;margin-bottom:3px}
  .schedule p{color:var(--white)}

  .panel--faq{background:var(--white)}
  .faq h3{font-size:8.6px;font-weight:700;margin-bottom:5px}
  .faq p{font-size:7.8px}
  .contact{position:absolute;left:0;right:0;top:361px;height:88px;background:var(--salmon);text-align:center;color:var(--white);padding-top:14px;z-index:2}
  .contact h3{font-size:11px;letter-spacing:.5px;margin-bottom:3px}
  .contact p{font-size:7px;line-height:1.35}

  .panel--cover{background:var(--gray-dark)}
  .cover-brand{position:absolute;left:14px;top:52px;width:175px;height:88px;background:var(--green-pale);display:flex;align-items:center;justify-content:center;z-index:3}
  .cover-brand .wordmark{position:static;font-size:22px;color:var(--teal-dark);gap:6px}
  .cover-brand .wordmark__dot{width:14px;height:14px}
  .tagline{position:absolute;left:14px;top:362px;color:var(--white);font-style:italic;font-size:10px;line-height:1.25;z-index:3;text-align:center;width:120px}

  /* Inside sheet */
  .panel--about{background:var(--white)}
  .about h2{font-size:12.5px;font-weight:700;margin-bottom:5px}
  .about p{font-size:7.8px}
  .panel--homecare{background:var(--salmon)}
  .homecare h2{color:var(--teal-dark);font-size:13px;text-align:center;margin-bottom:8px}
  .homecare p{color:var(--white);font-size:7.8px;margin-bottom:7px}
  .homecare .list-title{font-weight:700;margin-bottom:0}
  .homecare ul{list-style:none;color:var(--white);font-size:7.8px;padding-left:4px}
  .panel--care{background:var(--white)}
  .care p{font-size:7.8px}
  .care ul{list-style:none;font-size:7.8px;padding-left:8px;margin-bottom:4px}
  .care h2{color:var(--coral);font-size:12.5px;margin-bottom:3px}
  .care .label{color:var(--coral);font-weight:700}
  .care .block{margin-top:7px}
</style>
</head>
<body>

<!-- Outside: services flap, FAQ, cover -->
<section class="sheet sheet--outside" aria-label="Brochure outside">
  <article class="panel panel--services">
    <svg class="decor decor--top" width="233" height="70" viewBox="0 0 233 70" aria-hidden="true">
      <defs><linearGradient id="g-top-a" x1="0" x2="1"><stop offset="0" stop-color="#fff"/><stop offset="1" stop-color="#2c2c2c"/></linearGradient></defs>
      <rect width="233" height="70" fill="url(#g-top-a)"/>
      <path d="M0 70 L0 40 Q110 -5 233 18 L233 70Z" fill="var(--teal-light)"/>
      <path d="M0 48 Q110 4 233 22" stroke="var(--salmon)" stroke-width="4" fill="none"/>
    </svg>
    <div class="wordmark" style="right:10px;top:20px"><span class="wordmark__dot"></span>Brantley</div>
    <div class="content services-list" style="top:78px">
      <p><span class="label">Medication Services</span> – Our licensed nurse will pre-pour your medication in weekly pill containers for a 28-day period.</p>
      <p><span class="label">Transportation Services</span> – Our Care Professionals run errands or escort you to the grocery store, your personal appointments (physician, beautician, therapy), or other outings.</p>
    </div>
    <div class="content schedule" style="top:276px">
      <h2>Your Schedule</h2>
      <p>Brantley Homecare is flexible with your care needs. As you need more or less care, your schedule can be adjusted to accommodate your needs. We have found that a set schedule works best (same days and times each week). This allows you to be able to depend on the same care professional(s) each week. You determine the schedule, from a minimum of four hours per shift to 24 hours of care per day, 7 days per week, 365 days per year. Our Scheduling department is available 24 hours per day.</p>
    </div>
    <svg class="decor decor--bottom" width="233" height="62" viewBox="0 0 233 62" aria-hidden="true">
      <defs><linearGradient id="g-bot-a" x1="0" x2="1"><stop offset="0" stop-color="#e6e6e6"/><stop offset="1" stop-color="#2c2c2c"/></linearGradient></defs>
      <path d="M0 0 Q120 30 233 18 L233 62 L0 62Z" fill="url(#g-bot-a)"/>
    </svg>
    <span class="url">www.brantleycaregroup.example</span>
  </article>

  <article class="panel panel--faq">
    <svg class="decor decor--top" width="233" height="40" viewBox="0 0 233 40" aria-hidden="true">
      <path d="M0 0 L233 0 L233 8 Q120 -2 0 30Z" fill="var(--salmon-soft)"/>
      <path d="M40 0 L233 0 L233 22 Q150 2 40 0Z" fill="var(--gray-dark)" opacity=".85"/>
    </svg>
    <div class="wordmark" style="left:10px;top:8px;font-size:8px"><span class="wordmark__dot" style="width:5px;height:5px"></span>Brantley</div>
    <div class="content faq" style="top:58px">
      <h3>What makes Brantley Homecare different from other homecare agencies?</h3>
      <p>Answer: Brantley Homecare has earned a reputation in the community for providing compassionate, dependable, high -quality home care services. We employ Care Professionals who embody the Brantley vision of consistent, outstanding service for every client.</p>
    </div>
    <div class="content faq" style="top:282px">
      <h3>Are your employees screened?</h3>
      <p>Answer: All of our Care Professionals are pre-screened and submit to a comprehensive testing and assessment process which includes their criminal and driving abstracts, as well as screenings through Child/ Adult Protective Services.</p>
    </div>
    <div class="contact">
      <h3>CONTACT US</h3>
      <p>450 Harbor View Ave., Suite 210, Honolulu, HI 96813<br>Phone: (808) 555-0142<br>Fax (808) 555-0199<br>dana@brantleycare.example</p>
    </div>
    <svg class="decor decor--bottom" width="233" height="40" viewBox="0 0 233 40" aria-hidden="true">
      <path d="M0 0 L233 10 L233 40 L20 40Z" fill="var(--salmon)"/>
      <path d="M0 0 Q120 18 233 10" stroke="#c0392b" stroke-width="1" fill="none"/>
    </svg>
    <span class="url">www.brantleycaregroup.example</span>
  </article>

  <article class="panel panel--cover">
    <svg class="decor decor--top" width="233" height="482" viewBox="0 0 233 482" aria-hidden="true">
      <defs><linearGradient id="g-cover" x1="0" x2="1"><stop offset="0" stop-color="#8e8e8e"/><stop offset="1" stop-color="#1b1b1b"/></linearGradient></defs>
      <rect width="233" height="482" fill="url(#g-cover)"/>
      <path d="M0 0 L150 0 Q225 120 200 300 Q180 420 0 482Z" fill="var(--green-dark)"/>
      <path d="M0 0 L140 0 Q215 120 192 300 Q172 415 0 475Z" fill="var(--salmon)"/>
    </svg>
    <div class="photo" role="img" aria-label="Photo of a caregiver gently holding an elderly client's hands" style="left:0;top:0;width:188px;height:470px;border-radius:0 0 120px 0;background:linear-gradient(160deg,#c7d6ad 0%,#9cb97a 40%,#6f9a4f 70%,#cf9a80 100%);z-index:1"></div>
    <div class="cover-brand"><div class="wordmark"><span class="wordmark__dot"></span>Brantley</div></div>
    <p class="tagline">Some one you can depend<br>on without question......</p>
    <span class="url">www.brantleycaregroup.example</span>
  </article>

  <div class="photo-strip">
    <div class="photo" role="img" aria-label="Photo of a caregiver sharing a smile with an elderly client" style="left:0;width:142px;background:linear-gradient(135deg,#b9a493,#7d6555)"></div>
    <div class="photo" role="img" aria-label="Portrait photo of a smiling care professional" style="left:146px;width:170px;background:linear-gradient(135deg,#d8c2b0,#8c6a55)"></div>
    <div class="photo" role="img" aria-label="Photo of a caregiver assisting an elderly client at home" style="left:319px;width:142px;background:linear-gradient(135deg,#cbbfa8,#6d6a5a)"></div>
  </div>
</section>

<!-- Inside: about, services overview, care levels -->
<section class="sheet sheet--inside" aria-label="Brochure inside">
  <article class="panel panel--about">
    <svg class="decor decor--top" width="233" height="70" viewBox="0 0 233 70" aria-hidden="true">
      <defs><linearGradient id="g-top-d" x1="0" x2="1"><stop offset="0" stop-color="#fff"/><stop offset="1" stop-color="#2c2c2c"/></linearGradient></defs>
      <path d="M0 0 L233 0 L233 30 Q110 10 0 70Z" fill="url(#g-top-d)"/>
      <path d="M0 66 Q110 12 233 34" stroke="var(--salmon)" stroke-width="4" fill="none"/>
    </svg>
    <div class="wordmark wordmark--dark" style="right:10px;top:24px"><span class="wordmark__dot" style="background:var(--ink)"></span>Brantley</div>
    <div class="content about" style="top:64px">
      <h2>About Brantley Care Group</h2>
      <p>In 1996, Dana Brantley founded Brantley Homecare because of her own personal experience. Sixteen years later, in response to an overwhelming community need and countless client requests for a dedicated residential senior care home, she developed Brantley Senior Living. This is the second care resource offered under the expanded Brantley Care Group umbrella. With thousands of satisfied homecare clients, and now an exciting new healthcare alternative, Brantley Care Group continues to stay focused on what we do best: take care of those who need us.<br>Headquartered in Honolulu, Hawaii, the Brantley Care Group’s Administrative Offices are located at 450 Harbor View Avenue, Suite 210. The Group serves the island community of Oahu.</p>
    </div>
    <div class="photo" role="img" aria-label="Banner photo: “We’re here to help.” with the company founder beside an elderly client" style="left:0;top:258px;width:233px;height:74px;background:linear-gradient(90deg,#9a9a92,#d9d5cc 50%,#b04a45)"></div>
    <div class="content about" style="top:340px">
      <p>Dana Brantley, founder, president, and CEO of Brantley Care Group, discovered the need for dependable, compassionate home care at the tender age of 18, when she was seriously injured in an accident. Tragedy became inspiration, and in 1996, at the age of 21, she started Brantley Homecare.</p>
    </div>
    <svg class="decor decor--bottom" width="233" height="62" viewBox="0 0 233 62" aria-hidden="true">
      <defs><linearGradient id="g-bot-d" x1="0" x2="1"><stop offset="0" stop-color="#e6e6e6"/><stop offset="1" stop-color="#2c2c2c"/></linearGradient></defs>
      <path d="M0 0 Q120 34 233 18 L233 62 L0 62Z" fill="url(#g-bot-d)"/>
    </svg>
    <span class="url">www.brantleycaregroup.example</span>
  </article>

  <article class="panel panel--homecare">
    <svg class="decor decor--top" width="233" height="40" viewBox="0 0 233 40" aria-hidden="true">
      <defs><linearGradient id="g-top-e" x1="0" x2="1"><stop offset="0" stop-color="#fff"/><stop offset="1" stop-color="#1b1b1b"/></linearGradient></defs>
      <path d="M0 0 L233 0 L233 28 Q120 18 0 34Z" fill="url(#g-top-e)"/>
    </svg>
    <div class="wordmark" style="left:8px;top:10px;font-size:8.5px;color:var(--ink)"><span class="wordmark__dot" style="width:5px;height:5px"></span>Brantley</div>
    <div class="content homecare" style="top:52px">
      <h2>Brantley Home Care</h2>
      <p>Brantley Homecare is a state-licensed private duty home health care agency serving the island community of Oahu since 1996.</p>
      <p>We provide in-home services ranging from light housekeeping to personal care and skilled nursing. We strive to give compassionate, dependable care of the highest quality while maintaining extremely competitive rates. Everything we do is geared toward meeting the individual needs of our clients.</p>
      <p>Whether you need a little help or a lot of help, you’ll find that Brantley Homecare’s services are a cut above the rest. The Brantley Way is special; it is compassionate, professional, dependable, and flexible.</p>
      <p class="list-title">All of our Care Professionals:</p>
      <ul>
        <li>Are bonded, insured, and supervised;</li>
        <li>Have passed both criminal and abuse background checks;</li>
        <li>Have been screened for TB;</li>
        <li>Are certified in CPR and First Aid</li>
      </ul>
    </div>
    <div class="photo" role="img" aria-label="Photo of a nurse caring for a young child, captioned Quality homecare services, The Brantley Way" style="left:20px;top:341px;width:213px;height:84px;background:linear-gradient(90deg,#6b4f45,#c99c86 60%,#e9c9c2)"></div>
    <svg class="decor decor--bottom" width="233" height="58" viewBox="0 0 233 58" aria-hidden="true">
      <rect width="233" height="58" fill="#fff"/>
      <path d="M0 0 L233 0 L233 30 Q120 34 20 58 L0 58Z" fill="var(--salmon)"/>
      <path d="M0 8 Q120 24 233 12" stroke="#c0392b" stroke-width="1" fill="none"/>
    </svg>
    <span class="url" style="color:var(--ink)">www.brantleycaregroup.example</span>
  </article>

  <article class="panel panel--care">
    <svg class="decor decor--top" width="233" height="70" viewBox="0 0 233 70" aria-hidden="true">
      <defs><linearGradient id="g-top-f" x1="0" x2="1"><stop offset="0" stop-color="#9a9a9a"/><stop offset="1" stop-color="#1b1b1b"/></linearGradient></defs>
      <path d="M0 0 L233 0 L233 14 Q100 10 0 70Z" fill="url(#g-top-f)"/>
      <path d="M0 62 Q100 6 233 10" stroke="var(--green-dark)" stroke-width="6" fill="none"/>
    </svg>
    <div class="wordmark" style="right:10px;top:22px;font-size:8.5px;color:var(--coral)"><span class="wordmark__dot" style="width:5px;height:5px"></span>Brantley</div>
    <div class="content care" style="top:78px">
      <p>All client care is supervised by a licensed Nurse Care Consultant whose duties include:</p>
      <ul>
        <li>Regular home visits</li>
        <li>Client evaluation</li>
        <li>Care Professional supervision</li>
        <li>Revising/updating client care plans</li>
        <li>24/7 phone support</li>
      </ul>
      <h2>Services</h2>
      <p>Brantley Homecare provides two different levels of care. Our Nurse Care Consultant will assist the client and family in determining the appropriate level of care needed during the complimentary initial consultation.</p>
      <p class="block"><span class="label">Nurse Aide Care</span> - personal care needs, provide companionship, run errands, and do light housekeeping, along with assisting you with the activities of daily living.</p>
      <p class="block"><span class="label">Skilled Nursing Care</span> – We offer a wide range of skilled nursing services using RN’s and LPN’s who provide treatment from wound care to life support, in addition to all of the services performed by our Nurse Aides.</p>
    </div>
    <div class="photo" role="img" aria-label="Photo of caregivers spending time with elderly clients" style="left:0;top:341px;width:233px;height:84px;background:linear-gradient(90deg,#a9988a,#e4d6cc 50%,#9c6f72)"></div>
    <svg class="decor decor--bottom" width="233" height="58" viewBox="0 0 233 58" aria-hidden="true">
      <defs><linearGradient id="g-bot-f" x1="0" x2="1"><stop offset="0" stop-color="#e6e6e6"/><stop offset="1" stop-color="#2c2c2c"/></linearGradient></defs>
      <path d="M0 10 Q120 40 233 4 L233 58 L0 58Z" fill="url(#g-bot-f)"/>
    </svg>
    <span class="url">www.brantleycaregroup.example</span>
  </article>
</section>

</body>
</html>
```